Broschüren-Design für Unternehmen, das die Begrünung von Bürogebäuden anbietet
Wir sind mit der Zusammenarbeit mit inkmolde äußerst zufrieden. Vielen Dank für das ganze Mitdenken und die wichtigen Rückfragen an uns (Format, Layout, Farben, Papierwahl)! :)
Zielgruppe
Unser Kerngeschäft besteht in der Begrünung von Bürogebäuden.
Das heißt, wir liefern und pflegen exotische und tropische immergrüne Planzen für zum Beispiel Eingangsbereiche, Atrien, sowie Einzel- und Großraumbüros.
Die Zielgruppe besteht fast ausschließlich aus gewerblichen Kunden.
Aufgabenstellung
Die Vorlage ist ein grober Entwurf und Vorschlag von uns. Es darf davon auch gerne abgewichen werden.
Die Broschüre soll uns als Unterstützung für Erstgespräche bei potentiellen Neukunden dienen und verbleibt beim Kunden. Sie soll unsere Firma, uns als Menschen und unsere Produkte und Dienstleistung kurz präsentieren und einen guten Eindruck hinterlassen.
Danach wünschen wir uns idealerweise eine Kontaktaufnahme durch den Kunden selbst.

```html
<!DOCTYPE html>
<html lang="de">
<head>
<meta charset="utf-8">
<title>Wettberg Raumbegrünung – Leistungsportfolio</title>
<link href="https://fonts.googleapis.com/css2?family=Barlow:wght@400;600&family=Didact+Gothic&display=swap" rel="stylesheet">
<style>
  :root {
    --green: #5fad46;
    --ink: #3c3c3c;
    --text: #4a4a4a;
    --sun: #f2b400;
    --page: #ffffff;
    --backdrop: #eeeeee;
    --photo-top: #c9d3d6;
    --photo-mid: #9fb2a0;
    --photo-low: #b7443f;
  }
  * { box-sizing: border-box; margin: 0; padding: 0; }
  html, body { width: 1200px; height: 856px; overflow: hidden; }
  body { background: var(--backdrop); position: relative; font-family: "Didact Gothic", sans-serif; color: var(--text); }

  .spread { position: absolute; left: 115px; top: 86px; width: 970px; height: 684px; display: flex; }
  .page { position: relative; width: 485px; height: 684px; background: var(--page); }
  .page--left { border-right: 1px solid #e2e2e2; }

  .brand-name { position: absolute; left: 47px; top: 66px; font-family: "Barlow", sans-serif; font-weight: 400;
    color: var(--ink); font-size: 28px; line-height: 1; white-space: nowrap; }

  .section-tag { position: absolute; left: 0; top: 146px; width: 310px; height: 33px; background: var(--green); color: #fff;
    font-family: "Barlow", sans-serif; font-weight: 600; font-size: 16px; line-height: 33px; padding-left: 26px; }

  .plant-card { position: absolute; width: 171px; }
  .plant-photo { width: 171px; height: 175px;
    background: linear-gradient(180deg, var(--photo-top) 0%, var(--photo-mid) 48%, #8d9a84 62%, var(--photo-low) 78%, #c7c9c6 100%); }
  .plant-name { margin-top: 6px; height: 33px; background: var(--green); color: #fff; font-family: "Barlow", sans-serif;
    font-weight: 600; font-size: 15px; line-height: 33px; padding-left: 11px; }
  .plant-meta { margin-top: 16px; font-size: 9px; line-height: 1.2; }
  .plant-size { margin-top: 8px; font-size: 9px; line-height: 1.2; }
  .light-scale { margin-top: 5px; display: flex; justify-content: space-between; width: 160px; }
  .light-level { display: flex; flex-direction: column; align-items: center; font-size: 8.5px; gap: 2px; width: 52px; }
  .light-level svg { width: 26px; height: 26px; }
  .plant-traits { margin-top: 8px; font-size: 9px; line-height: 1.2; }
  .plant-notes { margin-top: 12px; font-size: 9px; line-height: 1.2; hyphens: auto; -webkit-hyphens: auto; }

  .footer-band { position: absolute; left: 0; right: 0; top: 648px; height: 24px; background: var(--green); }
  .footer-url { position: absolute; right: 14px; top: 0; line-height: 24px; color: #fff; font-size: 11px; letter-spacing: .3px; }
</style>
</head>
<body>
<svg width="0" height="0" style="position:absolute" aria-hidden="true">
  <defs>
    <g id="rays" stroke="var(--sun)" stroke-width="1.6" stroke-linecap="round">
      <line x1="14" y1="1.5" x2="14" y2="5"/><line x1="14" y1="23" x2="14" y2="26.5"/>
      <line x1="1.5" y1="14" x2="5" y2="14"/><line x1="23" y1="14" x2="26.5" y2="14"/>
      <line x1="5.2" y1="5.2" x2="7.6" y2="7.6"/><line x1="20.4" y1="20.4" x2="22.8" y2="22.8"/>
      <line x1="22.8" y1="5.2" x2="20.4" y2="7.6"/><line x1="7.6" y1="20.4" x2="5.2" y2="22.8"/>
    </g>
    <symbol id="sun-full" viewBox="0 0 28 28"><use href="#rays"/><circle cx="14" cy="14" r="6.5" fill="var(--sun)"/></symbol>
    <symbol id="sun-half" viewBox="0 0 28 28"><use href="#rays"/><circle cx="14" cy="14" r="6" fill="none" stroke="var(--sun)" stroke-width="1.4"/><path d="M14 8 A6 6 0 0 0 14 20 Z" fill="var(--sun)"/></symbol>
    <symbol id="sun-none" viewBox="0 0 28 28"><use href="#rays"/><circle cx="14" cy="14" r="6" fill="none" stroke="var(--sun)" stroke-width="1.4"/></symbol>
  </defs>
</svg>

<main class="spread">
  <section class="page page--left">
    <p class="brand-name">Wettberg Raumbegrünung</p>
    <h2 class="section-tag">Leistungsportfolio</h2>

    <article class="plant-card" style="left:46px; top:202px;">
      <div class="plant-photo" role="img" aria-label="Foto: Zimmerpflanze mit dichter Krone in rotem Kübel vor Glasfassade"></div>
      <h3 class="plant-name">Rhapis excelsa</h3>
      <p class="plant-meta">Beschreibung</p>
      <p class="plant-size">Tuff/Solitär/… 100cm/140cm/…</p>
      <div class="light-scale">
        <span class="light-level"><svg><use href="#sun-full"/></svg>Hell</span>
        <span class="light-level"><svg><use href="#sun-half"/></svg>halbschattig</span>
        <span class="light-level"><svg><use href="#sun-none"/></svg>schattig</span>
      </div>
      <p class="plant-traits">Besonders robust, resistent gegen Schädlinge, langlebig</p>
      <p class="plant-notes">(Schädlinge, Pflegeaufwand, allgemeine Beschreibung, lustiger Fakt (100 mal bei einem kunden, in der pflege teilweise 40 jahre alt, sansevieria früher in gastwirtschaften heute in Vorstandsbereichen, surculosa bambus-optik, …)</p>
    </article>

    <article class="plant-card" style="left:247px; top:202px;">
      <div class="plant-photo" role="img" aria-label="Foto: Steckenpalme in rotem Kübel vor Glasfassade"></div>
      <h3 class="plant-name">Rhapis excelsa</h3>
      <p class="plant-meta">Beschreibung</p>
      <p class="plant-size">Tuff/Solitär/… 100cm/140cm/…</p>
      <div class="light-scale">
        <span class="light-level"><svg><use href="#sun-full"/></svg>Hell</span>
        <span class="light-level"><svg><use href="#sun-half"/></svg>halbschattig</span>
        <span class="light-level"><svg><use href="#sun-none"/></svg>schattig</span>
      </div>
      <p class="plant-traits">Besonders robust, resistent gegen Schädlinge, langlebig</p>
      <p class="plant-notes">(Schädlinge, Pflegeaufwand, allgemeine Beschreibung, lustiger Fakt (100 mal bei einem kunden, in der pflege teilweise 40 jahre alt, sansevieria früher in gastwirtschaften heute in Vorstandsbereichen, surculosa bambus-optik, …)</p>
    </article>

    <div class="footer-band"></div>
  </section>

  <section class="page page--right">
    <article class="plant-card" style="left:58px; top:194px;">
      <div class="plant-photo" role="img" aria-label="Foto: Zimmerpflanze mit dichter Krone in rotem Kübel vor Glasfassade"></div>
      <h3 class="plant-name">Rhapis excelsa</h3>
      <p class="plant-meta">Beschreibung</p>
      <p class="plant-size">Tuff/Solitär/… 100cm/140cm/…</p>
      <div class="light-scale">
        <span class="light-level"><svg><use href="#sun-full"/></svg>Hell</span>
        <span class="light-level"><svg><use href="#sun-half"/></svg>halbschattig</span>
        <span class="light-level"><svg><use href="#sun-none"/></svg>schattig</span>
      </div>
      <p class="plant-traits">Besonders robust, resistent gegen Schädlinge, langlebig</p>
      <p class="plant-notes">(Schädlinge, Pflegeaufwand, allgemeine Beschreibung, lustiger Fakt (100 mal bei einem kunden, in der pflege teilweise 40 jahre alt, sansevieria früher in gastwirtschaften heute in Vorstandsbereichen, surculosa bambus-optik, …)</p>
    </article>

    <article class="plant-card" style="left:259px; top:188px;">
      <div class="plant-photo" role="img" aria-label="Foto: Steckenpalme in rotem Kübel vor Glasfassade"></div>
      <h3 class="plant-name">Rhapis excelsa</h3>
      <p class="plant-meta">Beschreibung</p>
      <p class="plant-size">Tuff/Solitär/… 100cm/140cm/…</p>
      <div class="light-scale">
        <span class="light-level"><svg><use href="#sun-full"/></svg>Hell</span>
        <span class="light-level"><svg><use href="#sun-half"/></svg>halbschattig</span>
        <span class="light-level"><svg><use href="#sun-none"/></svg>schattig</span>
      </div>
      <p class="plant-traits">Besonders robust, resistent gegen Schädlinge, langlebig</p>
      <p class="plant-notes">(Schädlinge, Pflegeaufwand, allgemeine Beschreibung, lustiger Fakt (100 mal bei einem kunden, in der pflege teilweise 40 jahre alt, sansevieria früher in gastwirtschaften heute in Vorstandsbereichen, surculosa bambus-optik, …)</p>
    </article>

    <div class="footer-band"><span class="footer-url">www.wettberg-raumbegruenung.de</span></div>
  </section>
</main>
</body>
</html>
```